Start-Up für Training, Coaching & Consulting sucht modernes Webdesign!
Zielgruppe
Wer ist TAVI Training, Coaching & Consulting?
Wir führen Führungskräftetrainings durch, machen Privatkunden für Bewerbungen fit und unterstützen Unternehmen mit Verkaufstrainings. Wir entwickeln Persönlichkeiten im Coaching. Wir beraten Unternehmen und helfen ihnen dabei, ihre Geschäftsabläufe und Prozesse zu optimieren. Dabei steht unsere hohe Qualität im Mittelpunkt - gemeinsam mit unseren kreativen Trainingsmethoden. Unser Background (Diplom-Kaufleute und geprüfte Trainer) bietet dafür die passende Ausgangslage.
Was bedeutet TAVI?
Tavi ist Maori und bdeutet Kreis/Spirale. Er symbolisiert einen wachsenden Silberfarn und steht für persönliche Entwicklung und Entfaltung. Der Tavi ist einerseits unser Namensgeber und unser Logo, andererseits steht der Tavi aber auch für unsere Werte: Denn wir wollen unseren Kunden dabei helfen zu wachsen und sich weiterzuentwickeln - und dies auf eine hochqualitative und seriöse Art und Weise ohne den Eindruck von Esoterik oder Erlebnispädagogik zu vermitteln.
Aufgabenstellung
Modernes Design, das unsere Philosophie widerspiegelt: Wir möchten unseren Kunden auf seriöse und hochqualitative Weise weiterentwickeln. Wir stehen für nachhaltigen Lernerfolg, kreative Trainingsmethoden, Abwechslung, Spaß am Lernen, Qualität, Kompetenz, Fachwissen und Dynamik.
Layout:
1) Header: QMSR geprüfter Trainer, Menüpunkte (siehe Architektur)
2) Banner
3) 3 Teaser (Training, Coaching, Consulting) + Header + 2-3 Zeilen Text (+Icons)
>>> Sichtbarer Bereich auf Homepage: Menü, Banner, Teaser
4) "Warum Sie uns wählen sollten": 5 bullet points ohne weiteren Text
5) "Aus unserem Blog": Frame für 3 Blogartikel + Bild + Datum + Header + 2-3 Zeilen Text
6) Alle drei QMSR Logos
7) Footer: Click Us (quick links), Contact Us (Adresse), Follow Us (Pinnwald, ZOLP, Kontaktor)
8) Copyright + Impressum
>>> Das Design soll klar sein, aber nicht zu kantig. Vielmehr sollen abgerundete Ecken und dynamische Elemente genutzt werden.
Architektur:
3 Ebenen:
1) Homepage
2) TAVI, Training, Coaching, Consulting, für Trainer, Kundenstimmen/Referenzen, Kontakt
3) noch zu bestimmende Produktdetailseiten
Texte werden noch erstellt, Layout kann ggf. mit Platzhaltertext gefüllt werden.
Bildmaterial: Logo und vorhandenes Imagebild werden zur Verfügung gestellt. Bilder können ggf. gekauft werden. Vorschläge erwünscht.
Corporate colors:
grün: #a2c61b + monochromatic colors
http://www.tintoskop.de/a2c61b
grau: #474747 + monochromatic colors
http://www.tintoskop.de/474747

```html
<!DOCTYPE html>
<html lang="de">
<head>
<meta charset="utf-8">
<title>TAVI Training, Coaching &amp; Consulting</title>
<link href="https://fonts.googleapis.com/css2?family=Mulish:wght@300;400;600;700;800&display=swap" rel="stylesheet">
<style>
:root{
  --green:#a2c61b;
  --green-light:#d8f25a;
  --green-dark:#5f8a1e;
  --grey:#474747;
  --grey-mid:#6b6b6b;
  --footer:#2b2d31;
  --white:#ffffff;
  --badge:#1c5fa8;
}
*{margin:0;padding:0;box-sizing:border-box}
html,body{width:795px;height:1200px;overflow:hidden;background:var(--white)}
body{position:relative;font-family:"Mulish",sans-serif;color:var(--grey)}
.abs{position:absolute}

/* hero */
.hero{left:0;top:0;width:795px;height:335px;
  background:radial-gradient(ellipse at 50% 55%,#7fae3a 0%,#4f8a26 45%,#2f5e1a 100%)}
.hero-wave{left:0;top:250px}
.topbar{left:0;top:0;width:795px;height:53px;background:rgba(40,44,40,.72)}
.brand{left:108px;top:10px;color:var(--white);font-weight:800;font-size:23px;letter-spacing:1px;display:flex;align-items:center;gap:4px}
.brand .dot{width:11px;height:11px;border-radius:50%;background:var(--green)}
.brand-tag{left:109px;top:38px;font-size:4.5px;color:var(--green-light)}
.cert-badge{left:201px;top:20px;width:67px;height:18px;background:var(--badge);border-radius:1px}
.nav{left:351px;top:0;height:53px;display:flex;align-items:center;font-size:9px;color:var(--white);font-weight:400}
.nav a{color:var(--white);text-decoration:none;height:53px;display:flex;align-items:center}
.nav .active{background:#23272a;color:var(--green);padding:0 9px;border-bottom:2px solid var(--green)}
.nav .sep{margin:0 18px;color:var(--white)}
.nav .caret{color:var(--green);margin-left:4px;font-size:7px}
.hero-title{left:0;width:795px;top:117px;text-align:center;color:var(--white);font-weight:300;font-size:31px;line-height:36px}
.hero-title b{font-weight:800}
.hero-sub{left:0;width:795px;top:187px;text-align:center;color:var(--white);font-size:13px;font-weight:400}
.hero-btn{left:351px;top:215px;width:100px;height:33px;border-radius:17px;background:var(--green);color:var(--white);font-size:8px;font-weight:700;display:flex;align-items:center;justify-content:center}
.arrow{top:152px}

/* teasers */
.teaser{top:352px;width:160px;text-align:center}
.teaser .photo{width:126px;height:126px;border-radius:50%;margin:0 auto}
.teaser h3{margin-top:17px;color:var(--green);font-size:9.5px;font-weight:700;padding-bottom:6px;border-bottom:1px dotted var(--green);width:142px;margin-left:auto;margin-right:auto}
.teaser p{margin-top:5px;font-size:7px;line-height:10.5px;color:var(--grey-mid);font-weight:300}

.divider{left:83px;width:635px;height:1px;background:#dfe5c9}
.divider-mark{width:22px;height:22px;border-radius:50%;background:var(--green-light)}

/* why */
.section-title{top:622px;color:var(--green);font-size:17px;font-weight:400;padding-bottom:8px;border-bottom:1px dotted var(--green)}
.why-list{left:118px;top:664px;list-style:none}
.why-list li{display:flex;align-items:center;height:29.6px;color:var(--green);font-size:12.5px;font-weight:400}
.why-list .tick{width:15px;height:15px;border-radius:50%;background:var(--green);margin-right:11px;display:flex;align-items:center;justify-content:center}

/* blog */
.post{left:465px;width:198px;height:68px;border-bottom:1px dotted var(--green)}
.post .thumb{position:absolute;left:2px;top:0;width:37px;height:37px;border-radius:50%}
.post p{position:absolute;left:56px;top:0;width:145px;font-size:7px;line-height:10.5px;color:var(--grey-mid);font-weight:300}
.post .more{position:absolute;left:53px;top:35px;width:38px;height:12px;border-radius:6px;background:var(--green);color:var(--white);font-size:6.5px;display:flex;align-items:center;justify-content:center}

.partner{background:var(--badge)}

/* footer */
.footer{left:0;top:880px;width:795px;height:320px}
.f-brand{left:117px;top:1005px;color:var(--white);font-weight:800;font-size:15px;display:flex;align-items:center;gap:3px}
.f-brand .dot{width:8px;height:8px;border-radius:50%;background:var(--green)}
.f-tag{left:118px;top:1023px;font-size:3.6px;color:#c9c9c9}
.f-links{left:117px;top:1043px;list-style:none;color:#e2e2e2;font-size:8.5px}
.f-links li{height:16px}
.f-head{top:1044px;color:var(--green);font-size:8.5px}
.f-body{top:1059px;color:#cfcfcf;font-size:7px;line-height:12.7px;font-weight:300;white-space:nowrap}
.f-follow{left:604px;top:1044px;color:#d9d9d9;font-size:8.5px;letter-spacing:.3px}
.social{top:1061px;width:22px;height:22px;border-radius:50%;background:var(--green)}
.f-rule{left:72px;top:1134px;width:660px;border-top:1px dotted var(--green)}
.copy{left:0;width:795px;top:1152px;text-align:center;color:#9a9a9a;font-size:8px;line-height:13px;font-weight:300}
</style>
</head>
<body>

<div class="abs hero" role="img" aria-label="Nahaufnahme junger, sich entrollender Farnwedel in Grün"></div>
<svg class="abs hero-wave" width="795" height="90" viewBox="0 0 795 90">
  <path d="M0 40 C120 10 230 15 340 45 C460 80 600 90 795 15 L795 90 L0 90 Z" fill="#fff"/>
</svg>

<header>
  <div class="abs topbar"></div>
  <div class="abs brand">TAVI<span class="dot"></span></div>
  <div class="abs brand-tag">Training • Coaching • Consulting</div>
  <div class="abs cert-badge" aria-label="Zertifikatsabzeichen"></div>
  <nav class="abs nav">
    <a class="active">HOME</a><span class="sep">I</span>
    <a>ÜBER UNS<span class="caret">&#8744;</span></a><span class="sep" style="margin-left:8px">I</span>
    <a>FÜR TRAINERS<span class="caret">&#8744;</span></a><span class="sep" style="margin-left:4px">I</span>
    <a>REFERENZEN</a><span class="sep">I</span>
    <a>KONTAKT</a>
  </nav>
</header>

<section>
  <h1 class="abs hero-title">TRAINING, COACHING<br>CONSULTING <b>FÜR TRAINER</b></h1>
  <p class="abs hero-sub">Lorem ipsum dolor sit amet consectetur adipiscing elit.</p>
  <div class="abs hero-btn">MEHR ERFAHREN</div>
  <svg class="abs arrow" style="left:17px" width="28" height="45" viewBox="0 0 28 45"><path d="M23 4 L6 22.5 L23 41" fill="none" stroke="#fff" stroke-width="7" stroke-linecap="round" stroke-linejoin="round"/></svg>
  <svg class="abs arrow" style="left:741px" width="28" height="45" viewBox="0 0 28 45"><path d="M5 4 L22 22.5 L5 41" fill="none" stroke="#fff" stroke-width="7" stroke-linecap="round" stroke-linejoin="round"/></svg>
</section>

<section>
  <div class="abs teaser" style="left:129px">
    <div class="photo" role="img" aria-label="Gefaltete Hände auf einem Schreibtisch mit Notizbuch" style="background:radial-gradient(circle at 50% 40%,#b9cde6,#6f8fbf 60%,#3b4a63)"></div>
    <h3>LOREM IPSUM DOLOR SIT</h3>
    <p>Lorem ipsum dolor sit amet, consectetur adipiscing elit. In dapibus accumsan luctus.</p>
  </div>
  <div class="abs teaser" style="left:316px">
    <div class="photo" role="img" aria-label="Zwei Geschäftsleute schauen gemeinsam auf ein Tablet" style="background:radial-gradient(circle at 55% 45%,#e7e2dc,#b3aca6 55%,#3e3f44)"></div>
    <h3>ADIPISCING ELIT</h3>
    <p>Dolor sit amet, consectetur adipiscing elit. In dapibus accumsan luctus.</p>
  </div>
  <div class="abs teaser" style="left:500px">
    <div class="photo" role="img" aria-label="Hände mit Stift und Smartphone am Tisch" style="background:radial-gradient(circle at 50% 45%,#eef0f2,#c7cbd0 60%,#9a8a84)"></div>
    <h3>ELIT NON VEHICULA</h3>
    <p>Sit amet, consectetur adipiscing elit. In dapibus accumsan luctus.</p>
  </div>
</section>

<div class="abs divider" style="top:583px"></div>
<div class="abs divider-mark" style="left:388px;top:572px"></div>

<section>
  <h2 class="abs section-title" style="left:139px">WHY CHOOSE US</h2>
  <ul class="abs why-list">
    <li><span class="tick"><svg width="7" height="7" viewBox="0 0 7 7"><path d="M2.5 1 L5 3.5 L2.5 6" fill="none" stroke="#fff" stroke-width="1.4"/></svg></span>Vestibulum nec mauris facilisis</li>
    <li><span class="tick"><svg width="7" height="7" viewBox="0 0 7 7"><path d="M2.5 1 L5 3.5 L2.5 6" fill="none" stroke="#fff" stroke-width="1.4"/></svg></span>Curabitur et tristique diam, nec sagittis nibh</li>
    <li><span class="tick"><svg width="7" height="7" viewBox="0 0 7 7"><path d="M2.5 1 L5 3.5 L2.5 6" fill="none" stroke="#fff" stroke-width="1.4"/></svg></span>Denim nec sagittis nibh</li>
    <li><span class="tick"><svg width="7" height="7" viewBox="0 0 7 7"><path d="M2.5 1 L5 3.5 L2.5 6" fill="none" stroke="#fff" stroke-width="1.4"/></svg></span>Vestibulum nec mauris facilisis</li>
    <li><span class="tick"><svg width="7" height="7" viewBox="0 0 7 7"><path d="M2.5 1 L5 3.5 L2.5 6" fill="none" stroke="#fff" stroke-width="1.4"/></svg></span>Tristique diam nec lorem</li>
  </ul>
</section>

<section>
  <h2 class="abs section-title" style="left:469px">BLOG</h2>
  <article class="abs post" style="top:668px">
    <div class="thumb" role="img" aria-label="Geschäftsleute im Gespräch" style="background:radial-gradient(circle,#d9d3cc,#4a4d55)"></div>
    <p>Lorem ipsum dolor sit amet, consectetur adipiscing elit. In dapibus accumsan luctus. Aliquam posuere eros sed nibh sagittis,</p>
    <div class="more">more</div>
  </article>
  <article class="abs post" style="top:736px">
    <div class="thumb" role="img" aria-label="Geschäftsmann mit Brille" style="background:radial-gradient(circle,#e4e1dd,#45474c)"></div>
    <p>Pellentesque habitant morbi tristique senectus et netus et malesuada fames ac turpis egestas.</p>
    <div class="more" style="top:36px">more</div>
  </article>
  <article class="abs post" style="top:804px;border-bottom:none">
    <div class="thumb" role="img" aria-label="Hände mit Smartphone" style="background:radial-gradient(circle,#eef0f2,#a89a94)"></div>
    <p>Mauris sollicitudin felis aliquam ipsum dictum vehicula. Donec feugiat sapien nunc, quis auctor libero finibus in.</p>
    <div class="more">more</div>
  </article>
</section>

<div class="abs divider" style="top:891px;width:607px"></div>
<div class="abs divider-mark" style="left:388px;top:880px"></div>

<svg class="abs footer" width="795" height="320" viewBox="0 0 795 320">
  <path d="M0 68 C140 40 260 90 420 95 C590 100 700 60 795 12 L795 320 L0 320 Z" fill="#c7ea3a"/>
  <path d="M0 80 C150 60 270 105 420 110 C590 115 700 80 795 45 L795 320 L0 320 Z" fill="#a2c61b"/>
  <path d="M0 95 C160 90 280 130 420 130 C590 130 700 100 795 70 L795 320 L0 320 Z" fill="#2b2d31"/>
</svg>

<div class="abs partner" style="left:279px;top:937px;width:66px;height:18px"></div>
<div class="abs partner" style="left:375px;top:930px;width:24px;height:32px"></div>
<div class="abs partner" style="left:453px;top:930px;width:24px;height:32px"></div>

<footer>
  <div class="abs f-brand">TAVI<span class="dot"></span></div>
  <div class="abs f-tag">Training • Coaching • Consulting</div>
  <ul class="abs f-links">
    <li>HOME</li><li>ÜBER UNS</li><li>FÜR TRAINERS</li><li>REFERENZEN</li><li>KONTAKT</li>
  </ul>

  <svg class="abs" style="left:204px;top:1042px" width="14" height="12" viewBox="0 0 14 12"><path d="M7 0 L14 6 L12 6 L12 12 L8.5 12 L8.5 8 L5.5 8 L5.5 12 L2 12 L2 6 L0 6 Z" fill="#a2c61b"/></svg>
  <div class="abs f-head" style="left:230px">Address</div>
  <div class="abs f-body" style="left:230px">Lindenweg 14<br>Haus B, 2. OG<br>34127 Musterstadt</div>

  <svg class="abs" style="left:335px;top:1042px" width="12" height="12" viewBox="0 0 12 12"><rect width="12" height="12" rx="2" fill="#a2c61b"/><path d="M3.5 2.5 L5 4.5 L4.2 5.5 C4.8 6.8 5.5 7.5 6.5 8 L7.5 7.2 L9.5 8.5 L8.5 9.8 C5.5 9.5 2.5 6.5 2.3 3.5 Z" fill="#2b2d31"/></svg>
  <div class="abs f-head" style="left:361px">Phone</div>
  <div class="abs f-body" style="left:361px">(000 &nbsp;555 &nbsp;0142 318<br>(000 &nbsp;555 &nbsp;0187 264<br>(000 &nbsp;555 &nbsp;0193 407</div>

  <svg class="abs" style="left:455px;top:1043px" width="14" height="10" viewBox="0 0 14 10"><rect width="14" height="10" rx="1" fill="#a2c61b"/><path d="M0.5 0.8 L7 5.5 L13.5 0.8" fill="none" stroke="#2b2d31" stroke-width="1.2"/></svg>
  <div class="abs f-head" style="left:481px">Email</div>
  <div class="abs f-body" style="left:481px">info@tavi.com<br>addressinfo@tavi.com<br>emailadd@tavi.com</div>

  <div class="abs f-follow">BITTE FOLGEN</div>
  <div class="abs social" style="left:597px" aria-label="Pinnwald"></div>
  <div class="abs social" style="left:625px" aria-label="ZOLP"></div>
  <div class="abs social" style="left:653px" aria-label="Kontaktor"></div>

  <div class="abs f-rule"></div>
  <p class="abs copy">Aliquam at pulvinar mi. Nulla eget bibendum nisl. Integer consectetur quam ac purus pharetra pulvinar.<br>Aenean faucibus tortor ac tortor aliquet tincidunt. Mauris eget maximus urna.</p>
</footer>

</body>
</html>
```